Upmarket Dessert Lounge needs a Business Card Design

We are an upmarket dessert lounge needing a business card to match our image.

We want something that is simple yet beautiful, feminine, classy, sophisticated and elegant. We want it to stand out and don't mind if it is bold.

The design should include our logo and colours of red or maroon with gold highlights. We don't mind if black is used.

Marlow & Quince

Target Market(s)

For those who like to indulge or treat themselves and give in to their temptations on good quality desserts.

Industry/Entity Type

Business

Requirements
Must have
• Must include our logo and our name

Marlow & Quince

M & Q

```html
<!DOCTYPE html>
<html lang="en">
<head>
<meta charset="utf-8">
<title>Marlow &amp; Quince – Business Card</title>
<link rel="stylesheet" href="https://fonts.googleapis.com/css2?family=Libre+Baskerville:wght@400;700&family=Source+Sans+3:wght@400;600&display=swap">
<style>
  :root {
    --maroon: #7a1418;
    --gold: #f5d9a8;
    --gold-line: #f2c98e;
    --paper: #ffffff;
    --ink: #3a3a3a;
    --backdrop: #ece8e3;
  }
  * { margin: 0; padding: 0; box-sizing: border-box; }
  html, body { width: 1200px; height: 758px; overflow: hidden; }
  body {
    background: var(--backdrop);
    font-family: "Source Sans 3", Arial, sans-serif;
    position: relative;
  }
  .card {
    position: absolute;
    top: 214px;
    width: 540px;
    height: 330px;
    border-radius: 26px;
    overflow: hidden;
    box-shadow: 0 10px 28px rgba(60, 30, 20, 0.25);
  }
  /* Front */
  .card--front { left: 40px; background: var(--paper); }
  .front__brand {
    position: absolute;
    left: 30px; top: 92px;
    width: 230px;
    text-align: center;
    font-family: "Libre Baskerville", Georgia, serif;
    font-weight: 400;
    font-size: 25px;
    line-height: 1.25;
    color: var(--maroon);
  }
  .front__brand-dot {
    display: block;
    width: 12px; height: 12px;
    margin: 12px auto 0;
    border-radius: 50%;
    background: var(--maroon);
  }
  .front__divider {
    position: absolute;
    left: 292px; top: 34px;
    width: 2px; height: 150px;
    background: linear-gradient(to bottom, rgba(0,0,0,0.05), rgba(0,0,0,0.35), rgba(0,0,0,0.05));
  }
  .front__contact { position: absolute; left: 308px; top: 30px; }
  .contact__name {
    font-family: "Libre Baskerville", Georgia, serif;
    font-weight: 700;
    font-size: 19px;
    color: var(--maroon);
  }
  .contact__title { font-size: 15px; color: var(--ink); margin: 2px 0 14px; }
  .contact__list { list-style: none; }
  .contact__item {
    display: flex; align-items: center; gap: 6px;
    font-size: 14.5px; line-height: 20px; color: var(--ink);
  }
  .contact__item svg { width: 12px; height: 12px; fill: var(--ink); flex: none; }
  .front__band { position: absolute; left: 0; bottom: 0; width: 540px; height: 150px; }
  .front__address {
    position: absolute;
    left: 40px; bottom: 26px;
    font-size: 15px; line-height: 21px;
    color: #fff;
  }
  /* Back */
  .card--back { left: 620px; background: var(--maroon); }
  .back__monogram {
    position: absolute;
    left: 0; right: 0; top: 78px;
    text-align: center;
    font-family: "Libre Baskerville", Georgia, serif;
    font-size: 92px;
    line-height: 1;
    color: var(--gold);
  }
  .back__web {
    position: absolute;
    left: 0; right: 0; bottom: 46px;
    text-align: center;
    font-size: 22px;
    letter-spacing: 3px;
    color: #fff;
  }
</style>
</head>
<body>
  <section class="card card--front">
    <div class="front__brand">Marlow &amp; Quince<span class="front__brand-dot"></span></div>
    <div class="front__divider"></div>
    <div class="front__contact">
      <p class="contact__name">Your name</p>
      <p class="contact__title">Title</p>
      <ul class="contact__list">
        <li class="contact__item">
          <svg viewBox="0 0 12 12"><path d="M2.5 0.8l2 2-1 1.3c.6 1.4 1.7 2.5 3.1 3.1l1.3-1 2 2-1.1 1.6C5.3 9.6 2.4 6.7 0.9 1.9z"/></svg>987-654-3210</li>
        <li class="contact__item">
          <svg viewBox="0 0 12 12"><rect x="3" y="0.5" width="6" height="11" rx="1"/><rect x="4" y="2" width="4" height="6" fill="#fff"/></svg>987-654-3210</li>
        <li class="contact__item">
          <svg viewBox="0 0 12 12"><rect x="0.5" y="2.5" width="11" height="7"/><path d="M0.5 2.5L6 7l5.5-4.5" stroke="#fff" stroke-width="1" fill="none"/></svg>info@marlow&amp;quince.com</li>
        <li class="contact__item">
          <svg viewBox="0 0 12 12"><circle cx="6" cy="6" r="5.5"/><path d="M0.5 6h11M6 0.5v11M6 0.5c-3 3-3 8 0 11M6 0.5c3 3 3 8 0 11" stroke="#fff" stroke-width="0.8" fill="none"/></svg>www.marlow&amp;quince.com</li>
      </ul>
    </div>
    <svg class="front__band" viewBox="0 0 540 150" preserveAspectRatio="none" aria-hidden="true">
      <path d="M0 52 C120 30 260 38 380 22 C450 14 510 4 540 0 L540 150 L0 150Z" fill="var(--gold-line)"/>
      <path d="M0 60 C120 38 260 46 380 30 C450 22 510 12 540 8 L540 150 L0 150Z" fill="var(--paper)"/>
      <path d="M0 66 C120 44 260 52 380 36 C450 28 510 18 540 14 L540 150 L0 150Z" fill="var(--maroon)"/>
    </svg>
    <p class="front__address">Street Name, City Name<br>State Zip Code</p>
  </section>

  <section class="card card--back">
    <div class="back__monogram">M &amp; Q</div>
    <p class="back__web">www.marlow&amp;quince.com</p>
  </section>
</body>
</html>
```